5 website banners (slides show)

We need 5 website sliding banners created for a website all about internet safety. The topics for each banner are:

Cyberbullying
Fraud
seniors
social networking

Sizes: 953 pixels x 281 pixels

I have stock images to use or feel free to use your own or one I can purchase from pixelharbor.example.

Industry/Entity Type

Internet

```html
<!DOCTYPE html>
<html lang="en">
<head>
<meta charset="utf-8">
<title>Netwise – Online Safety and Security</title>
<link rel="stylesheet" href="https://fonts.googleapis.com/css2?family=Ubuntu:wght@400;500;700&family=Ubuntu+Condensed&family=Playball&family=Arimo:wght@400&display=swap">
<style>
  :root {
    --pink: #ec008c;
    --pink-soft: #e055a8;
    --green: #8cc63f;
    --green-dark: #6fae2a;
    --green-nav: #7bbd2f;
    --grey-text: #8a94a0;
    --white: #ffffff;
  }
  * { box-sizing: border-box; margin: 0; padding: 0; }
  html, body { width: 1200px; height: 900px; overflow: hidden; background: var(--white); }
  body { position: relative; font-family: "Arimo", Arial, sans-serif; }

  .utility-bar { position: absolute; left: 128px; top: 7px; width: 950px; height: 34px; background: var(--pink); border-radius: 5px; }
  .utility-links { position: absolute; left: 15px; top: 8px; display: flex; gap: 25px; list-style: none; }
  .utility-links li { color: var(--white); font-size: 13px; }
  .social-square { position: absolute; left: 610px; top: 5px; width: 24px; height: 24px; background: #3b5998; border-radius: 3px; }
  .search-field { position: absolute; left: 639px; top: 2px; width: 280px; height: 30px; background: var(--white); color: #b8a2c2; font-size: 12px; padding: 8px 12px; }
  .search-button { position: absolute; left: 919px; top: 4px; width: 27px; height: 26px; background: var(--pink); border-radius: 3px; }

  .brand { position: absolute; left: 145px; top: 55px; display: flex; align-items: center; }
  .brand-mark { width: 96px; height: 107px; border-radius: 50%; background: #f7d6ea; border: 5px solid var(--pink); }
  .brand-name { position: absolute; left: 113px; top: 8px; font-family: "Ubuntu Condensed", sans-serif; font-size: 60px; line-height: 1; color: var(--pink); white-space: nowrap; }
  .brand-tagline { position: absolute; left: 115px; top: 70px; font-family: "Ubuntu Condensed", sans-serif; font-size: 14px; color: var(--green-dark); white-space: nowrap; }

  .report-card { position: absolute; left: 722px; top: 63px; width: 356px; height: 96px; background: linear-gradient(#9ed050, var(--green)); border-radius: 3px; }
  .report-card::before { content: ""; position: absolute; inset: 6px; border: 1px dashed rgba(255,255,255,.8); }
  .report-title { position: absolute; left: 17px; top: 14px; font-family: "Ubuntu", sans-serif; font-weight: 500; font-size: 21px; color: var(--white); }
  .report-click { position: absolute; left: 185px; top: 40px; font-family: "Ubuntu", sans-serif; font-size: 13px; color: var(--white); }
  .report-phone { position: absolute; left: 14px; top: 56px; font-family: "Ubuntu", sans-serif; font-weight: 500; font-size: 25px; color: var(--white); }
  .report-badge { position: absolute; left: 268px; top: 5px; width: 70px; height: 86px; background: #6f8fb8; border-radius: 8px 8px 35px 35px; }

  .main-nav { position: absolute; left: 128px; top: 177px; width: 950px; height: 67px; background: var(--green-nav); border-radius: 5px; border-bottom: 10px solid #8ccc3a; }
  .main-nav ul { display: flex; list-style: none; height: 100%; }
  .main-nav li { font-family: "Ubuntu Condensed", sans-serif; font-size: 16px; color: var(--white); padding: 17px 19px 0 20px; border-right: 2px solid #9ccf5e; }
  .main-nav li.is-current { background: #8fcc48; border-radius: 5px 0 0 0; border-right: none; }

  .hero { position: absolute; left: 126px; top: 252px; width: 953px; height: 281px; }
  .hero-tag { position: absolute; left: 662px; top: 46px; font-family: "Ubuntu", sans-serif; font-size: 17px; color: var(--white); }
  .hero-title { position: absolute; left: 566px; top: 92px; width: 330px; text-align: center; font-family: "Playball", cursive; font-size: 40px; line-height: 60px; color: var(--white); }

  .issue-panel { position: absolute; left: 128px; top: 546px; width: 220px; height: 380px; background: var(--green); border-radius: 8px; }
  .issue-panel::before { content: ""; position: absolute; left: 10px; top: 10px; right: 10px; bottom: 0; border: 1px dashed rgba(255,255,255,.85); border-radius: 6px; }
  .issue-heading { position: absolute; left: 21px; top: 31px; font-family: "Ubuntu", sans-serif; font-weight: 500; font-size: 15px; color: var(--white); }
  .issue-list { position: absolute; left: 26px; top: 62px; list-style: none; }
  .issue-list li { font-size: 12px; color: var(--white); line-height: 25px; }

  .content { position: absolute; left: 358px; top: 546px; width: 717px; height: 360px; background: var(--white); box-shadow: 2px 0 4px rgba(0,0,0,.2); }
  .welcome-heading { position: absolute; left: 20px; top: 20px; font-family: "Ubuntu Condensed", sans-serif; font-size: 27px; color: var(--pink); }
  .edit-link { position: absolute; left: 35px; top: 56px; font-size: 12px; color: var(--pink-soft); }
  .edit-link::before { content: ""; position: absolute; left: -15px; top: 6px; width: 4px; height: 4px; border-radius: 50%; background: #9aa; }
  .welcome-text { position: absolute; left: 20px; top: 91px; width: 680px; font-size: 12px; line-height: 17px; color: var(--grey-text); }
  .welcome-text p + p { margin-top: 17px; }

  .audience { position: absolute; top: 286px; width: 200px; }
  .audience h3 { font-family: "Ubuntu Condensed", sans-serif; font-size: 16px; font-weight: 400; color: var(--pink); height: 21px; }
  .audience-photo { width: 200px; height: 60px; }
</style>
</head>
<body>
  <header>
    <div class="utility-bar">
      <ul class="utility-links"><li>Home</li><li>FAQs</li><li>Contact</li></ul>
      <div class="social-square" aria-label="Social page"></div>
      <div class="search-field">Search...</div>
      <div class="search-button" aria-label="Search">
        <svg width="27" height="26" viewBox="0 0 27 26"><circle cx="12" cy="12" r="6" fill="none" stroke="#fff" stroke-width="2.5"/><line x1="16.5" y1="16.5" x2="21" y2="21" stroke="#fff" stroke-width="3" stroke-linecap="round"/></svg>
      </div>
    </div>

    <div class="brand">
      <div class="brand-mark"></div>
      <div class="brand-name">NETWISE</div>
      <div class="brand-tagline">BERMUDA ONLINE SAFETY AND SECURITY</div>
    </div>

    <div class="report-card">
      <div class="report-title">REPORT A CYBERCRIME</div>
      <div class="report-click">CLICK HERE</div>
      <div class="report-phone">or call 1-555-010-2040</div>
      <div class="report-badge"></div>
    </div>

    <nav class="main-nav">
      <ul>
        <li class="is-current">HOME</li><li>ABOUT</li><li>FOR PARENTS</li><li>FOR TEENS</li><li>FOR TWEENS</li><li>FOR KIDS</li><li>FOR TEACHERS</li><li>RESOURCES</li>
      </ul>
    </nav>
  </header>

  <section class="hero">
    <svg width="953" height="281" viewBox="0 0 953 281">
      <defs>
        <linearGradient id="photoTone" x1="0" y1="0" x2="1" y2="1">
          <stop offset="0" stop-color="#d8cfc2"/><stop offset=".5" stop-color="#c9a888"/><stop offset="1" stop-color="#efe9e2"/>
        </linearGradient>
        <radialGradient id="circuitTone" cx=".6" cy=".5" r=".7">
          <stop offset="0" stop-color="#3aa52a"/><stop offset="1" stop-color="#0f4a12"/>
        </radialGradient>
      </defs>
      <rect width="953" height="281" fill="url(#circuitTone)" role="img" aria-label="Glowing green circuit board background"/>
      <polygon points="0,0 497,0 343,281 0,281" fill="url(#photoTone)" role="img" aria-label="Photo of a smiling child tapping a tablet"/>
      <polygon points="497,0 503,0 349,281 343,281" fill="#ffffff"/>
      <polygon points="503,0 509,0 355,281 349,281" fill="#1b5e1a"/>
    </svg>
    <div class="hero-tag">#Seniors</div>
    <div class="hero-title">Talking About the Digital World</div>
  </section>

  <aside class="issue-panel">
    <h2 class="issue-heading">CHOOSE AN ISSUE</h2>
    <ul class="issue-list">
      <li>Cyberbullying</li><li>Sexting</li><li>Internet Safety</li><li>Fraud</li><li>Mobile Devices</li><li>Gangs</li><li>Blogging</li><li>Predators</li><li>Copywriting</li><li>Social Networking</li><li>Gaming</li><li>eMailing, Chat Rooms</li>
    </ul>
  </aside>

  <main class="content">
    <h1 class="welcome-heading">WELCOME</h1>
    <span class="edit-link">Edit</span>
    <div class="welcome-text">
      <p>Welcome to Netwise, Bermuda’s source of information on internet safety, brought to you by the Ministry of Digital Affairs. Our aim is to provide practical tips, resources and contact information to help parents, children and educators to use the Internet safely and be on guard against online predators and other inappropriate online content.</p>
      <p>By knowing the dangers and how to avoid them, you can take advantage of all the positive aspects of the Internet while avoiding most of its pitfalls.</p>
      <p>The Ministry of Digital Affairs partners with the Island Police Service, Northwind Software, Pip’s Planet and a number of other organizations locally and internationally to bring innovative and media rich educational tools to Bermuda</p>
    </div>
    <div class="audience" style="left:10px"><h3>KIDS</h3><div class="audience-photo" role="img" aria-label="Photo of a young child at a computer" style="background:linear-gradient(#c89a78,#e8d8c8)"></div></div>
    <div class="audience" style="left:245px"><h3>TWEENS</h3><div class="audience-photo" role="img" aria-label="Photo of a preteen girl" style="background:linear-gradient(#8a7ab0,#5a3e34)"></div></div>
    <div class="audience" style="left:480px"><h3>TEENS</h3><div class="audience-photo" role="img" aria-label="Photo of a group of teenagers" style="background:linear-gradient(#b88a70,#6a4a3a)"></div></div>
  </main>
</body>
</html>
```